LEARN Business Skills so you can Earn a good living

size of the poster is 8”x 10.75" plus 0.25" bleed.
Please leave 1 inch on the bottoum for footer
I want a design a poster that will attract people's attention.
I appreciate a creative ad however the ad should not take away from being able to clearly read the text.
-I also appreciate a simple creative ad that is not too busy.
-you can use graphics, vectors, or pictures of real people.
-however, if you use real people it should be a white male that is wearing a white shirt and look like a professional person.

Target Market(s)

Potential young business people

Industry/Entity Type

education

Requirements
Must have
• easy to read the text
Nice to have
• I would like a "creative" simple ad that is easy to be read
Should not have
• pictures of women

```html
<!DOCTYPE html>
<html lang="en">
<head>
<meta charset="utf-8">
<title>Learn It To Earn It – Business Enrichment Course</title>
<link href="https://fonts.googleapis.com/css2?family=Bebas+Neue&display=swap" rel="stylesheet">
<style>
  :root {
    --page: #ffffff;
    --red: #c8181c;
    --red-deep: #a81216;
    --red-bright: #d41a1e;
    --white: #ffffff;
    --yellow: #ffe800;
  }
  html, body {
    margin: 0;
    padding: 0;
    width: 1200px;
    height: 1200px;
    overflow: hidden;
    background: var(--page);
  }
  .canvas {
    position: relative;
    width: 1200px;
    height: 1200px;
    font-family: "Bebas Neue", "Arial Narrow", sans-serif;
  }
  .poster {
    position: absolute;
    left: 269px;
    top: 144px;
    width: 669px;
    height: 920px;
    overflow: hidden;
    background:
      radial-gradient(ellipse at 30% 40%, var(--red-bright) 0%, transparent 60%),
      radial-gradient(ellipse at 85% 90%, var(--red-deep) 0%, transparent 55%),
      radial-gradient(ellipse at 10% 95%, var(--red-deep) 0%, transparent 45%),
      radial-gradient(ellipse at 95% 10%, var(--red-deep) 0%, transparent 40%),
      var(--red);
  }
  .poster > * {
    position: absolute;
    margin: 0;
    line-height: 1;
    white-space: nowrap;
  }
  .headline {
    font-size: 126px;
    font-weight: 400;
    color: var(--white);
  }
  .headline--top { left: 81px; top: 68px; }
  .headline-box {
    left: 68px;
    top: 177px;
    width: 426px;
    height: 107px;
    background: var(--white);
    border-radius: 6px;
  }
  .headline--boxed { left: 78px; top: 173px; color: var(--red); }
  .course-title {
    left: 206px;
    font-size: 62px;
  }
  .course-title--white { top: 319px; color: var(--white); }
  .course-title--yellow { top: 372px; color: var(--yellow); }
  .rule {
    left: 68px;
    width: 152px;
    height: 7px;
    background: var(--yellow);
  }
  .rule--upper { top: 444px; }
  .rule--lower { top: 543px; }
  .claim {
    left: 68px;
    font-size: 37px;
    color: var(--white);
  }
  .claim--one { top: 463px; }
  .claim--two { top: 500px; }
  .benefit {
    left: 155px;
    font-size: 40px;
    color: var(--white);
  }
  .benefit--job { top: 577px; }
  .benefit--business { top: 615px; }
  .benefit--salary { top: 653px; }
  .benefit-dash {
    left: 112px;
    width: 22px;
    height: 8px;
    background: var(--yellow);
  }
  .benefit-dash--job { top: 591px; }
  .benefit-dash--business { top: 629px; }
  .benefit-dash--salary { top: 667px; }
  .subjects {
    left: 0;
    width: 669px;
    top: 729px;
    text-align: center;
    font-size: 13px;
    line-height: 19.5px;
    color: var(--white);
  }
  .footer-rule {
    left: 272px;
    top: 801px;
    width: 125px;
    height: 1.5px;
    background: var(--yellow);
  }
</style>
</head>
<body>
<div class="canvas">
  <section class="poster">
    <h1 class="headline headline--top">LEARN IT</h1>
    <div class="headline-box"></div>
    <p class="headline headline--boxed">TO EARN IT</p>

    <h2 class="course-title course-title--white">BUSINESS</h2>
    <p class="course-title course-title--yellow">ENRICHMENT COURSE</p>

    <div class="rule rule--upper"></div>
    <p class="claim claim--one">A PROVEN SUCCESS OF HELPING</p>
    <p class="claim claim--two">PEOPLE IN THEIR LIVELIHOODS</p>
    <div class="rule rule--lower"></div>

    <div class="benefit-dash benefit-dash--job"></div>
    <p class="benefit benefit--job">GET A QUALITY JOB</p>
    <div class="benefit-dash benefit-dash--business"></div>
    <p class="benefit benefit--business">START/GROW YOUR BUSINESS</p>
    <div class="benefit-dash benefit-dash--salary"></div>
    <p class="benefit benefit--salary">INCREASE YOUR SALARY</p>

    <p class="subjects">BUSINESS ADMINISTRATION - SMALL BUSINESS MANAGEMENT - FINANCE - INVESTMENTS - COMPUTERS - ACCOUNTING - SALES -<br>MARKETING - PROJECT MANAGEMENT INTERVIEWING SKILLS - BUSINESS LAW - NEGOTIATION - PUBLIC SPEAKING - IMPORT/EXPORT -<br>INFORMATION TECHNOLOGY - DISTRIBUTION - MARKETING - LEDGERPRO - REAL ESTATE - HEALTH CARE - MANAGEMENT - SHOPWAVE</p>

    <div class="footer-rule"></div>
  </section>
</div>
</body>
</html>
```